High-Converting Facebook Ads for Portals Drapes & Louvres (6 Products)

We are looking for a graphic designer to create high-quality Facebook & Instagram ads for our business: Portals Drapes and Louvres (Melbourne, Australia).

We require 6 separate ad designs, each for a different product:

Zipscreen Blinds

Outdoor Awnings

Plantation Shutters

Roller Shutters

Security Doors

Roller Blinds & Sheer Curtains

Ad Specifications:

Sizes:

1440 x 1800 px (4:5 ratio)

1080 x 1080 px (1:1 ratio)

1080 x 1920 px (9:16 ratio for Stories/Reels)

Format: PNG (high resolution, not blurry)

Designed specifically for Meta (Facebook/Instagram ads)

Mobile-friendly layout (clear, easy to read)

Style:

Bold, sales-driven, retail-style ads (NOT minimal)

Eye-catching and designed to generate leads

Clean, professional layout

Similar to promotional home improvement ads

Brand Colours:

Red: #E31E24

Blue: #0072BC

White backgrounds

Each ad must include:

“SALE NOW ON” banner at top

Our showroom address:
482 Upper Wattleby Road, Kestrel Heights (must be fully visible, not cut off)

Phone number: 9471 2658

Our logo (provided)

Badge: “Celebrating 13 YEARS in Business” (must be clean and readable)

Call to Action:

For 5 ads: “Book a FREE quote TODAY!”

For Security Doors ad: “ORDER NOW”

Offers / Pricing:

Most products: “UP TO 40% OFF”

Plantation Shutters: “FROM $299/sqm”

Security Doors: “FROM $750”

Content for each ad (examples):

Zipscreen Blinds:

Made to Measure

Fully Installed

Wind, Sun & Insect Protection

Outdoor Awnings:

Reduce Heat & Glare

Energy Saving

Custom Made

Plantation Shutters:

Modern & Elegant

Light & Privacy Control

Durable & Easy Care

Roller Shutters:

Security Protection

Block Heat & Noise

Total Light Control

Security Doors:

3 Point Locking

Premium Mesh

Custom Made

Blinds & Sheers:

Huge Range of Fabrics

Modern Soft Finish

Perfect for Any Room

Important Notes:

All text must be sharp and easy to read (no blur)

Layout must be balanced and not overcrowded

Ensure no text is cut off (especially address and headings)

Badge text must be straight and professional (no distortion)

Use high-quality, relevant images (we will provide references)

Goal:
Create ads that look professional, trustworthy, and generate enquiries/bookings for in-home quotes.

We are open to creative ideas but want a strong, bold retail-style ad that converts.
I have uploaed chatgpt mocks

Target Market(s)

Homeowners in Melbourne, Australia (typically aged 30–65) looking to improve their homes with blinds, shutters, awnings and security doors. Mid to high income households focused on quality, security, and modern home upgrades.

Industry/Entity Type

Home Improvement / Construction / Retail

Font styles to use
Sans Serif

Requirements
Must have
• Clear, bold and easy-to-read text (must be readable on mobile) High-quality, non-blurry design Strong “SALE” style layout (retail promotional look) Proper spacing (no overcrowded designs) All key info visible (address must NOT be cut off) Correct pricing and offers included Clean “13 YEARS” badge (no distortion or curved text) Consistent branding across all 6 ads
Nice to have
• Modern, slightly premium feel while still being bold Good use of contrast (red/blue/white) Subtle shadows or layering to improve depth Clean use of icons or bullet points Strong hierarchy (headline → benefits → offer → CTA) Variations in layout for testing different ad styles
Should not have
• Minimal or plain designs (we want bold, sales-driven ads) Hard-to-read fonts or script fonts Low-quality or blurry images Overcrowded layouts with too much text Important text cut off (especially address or headings) Overuse of effects or “cheap” looking graphics Yellow-heavy colour schemes (must follow brand colours)

```html
<!DOCTYPE html>
<html lang="en">
<head>
<meta charset="utf-8">
<title>Portals Drapes &amp; Louvres – Story Ads 9:16</title>
<link href="https://fonts.googleapis.com/css2?family=Anton&family=Oswald:wght@600;700&family=Russo+One&family=Poppins:wght@500;600&display=swap" rel="stylesheet">
<style>
  :root{
    --brand-red:#E31E24;
    --brand-blue:#0072BC;
    --white:#ffffff;
    --board:#000000;
    --title-grey:#4a4a4a;
    --ink:#1d1d1d;
  }
  *{margin:0;padding:0;box-sizing:border-box}
  html,body{width:996px;height:1200px;overflow:hidden;background:var(--board)}
  .board{position:relative;width:996px;height:1200px;background:var(--board)}
  .board-title{
    position:absolute;left:0;right:0;top:126px;text-align:center;
    font-family:"Anton",sans-serif;font-size:58px;line-height:1;color:var(--title-grey);letter-spacing:0.5px;
  }
  .ad{position:absolute;width:235px;height:419px;background:var(--white);overflow:hidden}
  .ad-header{
    position:absolute;left:0;top:0;width:100%;height:50px;background:var(--brand-red);
    color:var(--white);font-family:"Oswald",sans-serif;font-weight:700;font-size:40px;line-height:50px;
    text-align:center;letter-spacing:-0.5px;
  }
  .ad-visual{position:absolute;left:0;top:0;width:235px;height:240px}
  .product-ribbon{
    position:absolute;left:28px;top:240px;width:179px;height:23px;
    background:linear-gradient(90deg,rgba(227,30,36,0) 0%,var(--brand-red) 12%,var(--brand-red) 88%,rgba(227,30,36,0) 100%);
    color:var(--white);font-family:"Oswald",sans-serif;font-weight:600;font-size:9.5px;line-height:23px;text-align:center;letter-spacing:0.2px;
  }
  .benefits{position:absolute;left:0;right:0;top:272px;list-style:none;display:flex;flex-direction:column;align-items:center}
  .benefits-inner{display:flex;flex-direction:column;gap:3.6px}
  .benefit{font-family:"Poppins",sans-serif;font-weight:500;font-size:7px;line-height:8px;color:var(--ink);display:flex;align-items:center;gap:5px;white-space:nowrap}
  .benefit svg{width:7px;height:7px;flex:none}
  .cta{position:absolute;left:0;right:0;top:317px;text-align:center;font-family:"Russo One",sans-serif;font-size:13.5px;line-height:17px;color:var(--brand-red);white-space:nowrap}
  .cta.large{font-size:21px;top:311px}
  .offer{position:absolute;left:0;right:0;top:334px;text-align:center;font-family:"Russo One",sans-serif;font-size:24px;line-height:29px;color:var(--brand-blue);white-space:nowrap}
  .ad-footer{position:absolute;left:0;bottom:0;width:100%;height:50px;background:var(--brand-red);color:var(--white)}
  .footer-brand{position:absolute;left:8px;top:17px;width:74px;display:flex;align-items:center;gap:4px}
  .brand-mark{width:7px;height:7px;background:var(--white);flex:none}
  .brand-name{font-family:"Poppins",sans-serif;font-weight:600;font-size:6.5px;line-height:8px;color:var(--white)}
  .footer-phone{position:absolute;left:86px;top:5px;display:flex;align-items:center;gap:4px;font-family:"Russo One",sans-serif;font-size:21px;line-height:26px;letter-spacing:1px;white-space:nowrap}
  .footer-phone svg,.footer-address svg{flex:none}
  .footer-address{position:absolute;left:86px;top:33px;display:flex;align-items:center;gap:5px;font-family:"Poppins",sans-serif;font-weight:500;font-size:6px;line-height:8px;white-space:nowrap}
</style>
</head>
<body>
<svg width="0" height="0" style="position:absolute" aria-hidden="true">
  <defs>
    <symbol id="bullet" viewBox="0 0 10 10">
      <path d="M5 0 L10 5 L5 10 L0 5 Z" fill="#E31E24" opacity="0.25"/>
      <path d="M5 2 L8 5 L5 8 L2 5 Z" fill="#0072BC"/>
      <path d="M5 3.5 L6.5 5 L5 6.5 L3.5 5 Z" fill="#E31E24"/>
    </symbol>
    <symbol id="phone" viewBox="0 0 12 12">
      <circle cx="6" cy="6" r="6" fill="#fff"/>
      <path d="M4 3 L5 3 L5.6 4.6 L4.9 5.2 C5.3 6.1 5.9 6.7 6.8 7.1 L7.4 6.4 L9 7 L9 8 C9 8.6 8.5 9 8 9 C5.2 8.8 3.2 6.8 3 4 C3 3.5 3.4 3 4 3 Z" fill="#E31E24"/>
    </symbol>
    <symbol id="pin" viewBox="0 0 12 12">
      <circle cx="6" cy="6" r="6" fill="#fff"/>
      <path d="M6 2.5 C4.5 2.5 3.5 3.6 3.5 5 C3.5 6.8 6 9.5 6 9.5 C6 9.5 8.5 6.8 8.5 5 C8.5 3.6 7.5 2.5 6 2.5 Z" fill="#E31E24"/>
      <circle cx="6" cy="5" r="1" fill="#fff"/>
    </symbol>
    <radialGradient id="badge-fill" cx="0.45" cy="0.4" r="0.6">
      <stop offset="0" stop-color="#e8c25a"/>
      <stop offset="1" stop-color="#a6741c"/>
    </radialGradient>
  </defs>
</svg>

<main class="board">
  <h1 class="board-title">1080 x 1920 px (9:16 ratio)</h1>

  <!-- Zipscreen Blinds -->
  <article class="ad" style="left:131px;top:227px">
    <svg class="ad-visual" viewBox="0 0 235 240">
      <defs><linearGradient id="g1" x1="0" y1="0" x2="0" y2="1"><stop offset="0" stop-color="#8c8f8e"/><stop offset="0.6" stop-color="#a7a39b"/><stop offset="1" stop-color="#5f8a3e"/></linearGradient></defs>
      <path d="M-3,103 A128,128 0 0 0 238,103" fill="none" stroke="#0072BC" stroke-width="6"/>
      <path d="M0,50 H235 V100 A123.7,123.7 0 0 1 0,100 Z" fill="url(#g1)" role="img" aria-label="Covered patio enclosed by outdoor zipscreen blinds"/>
      <circle cx="117.5" cy="191" r="38" fill="url(#badge-fill)" role="img" aria-label="Gold emblem: Celebrating 13 Years in Business"/>
    </svg>
    <div class="ad-header">SALE NOW ON</div>
    <div class="product-ribbon">ZIPSCREEN BLINDS</div>
    <ul class="benefits"><li class="benefits-inner">
      <span class="benefit"><svg><use href="#bullet"/></svg>Made to Measure</span>
      <span class="benefit"><svg><use href="#bullet"/></svg>Fully Installed</span>
      <span class="benefit"><svg><use href="#bullet"/></svg>Wind, Sun &amp; Insect Protection</span>
    </li></ul>
    <p class="cta">BOOK A FREE QUOTE TODAY!</p>
    <p class="offer">UP TO 40% OFF</p>
    <footer class="ad-footer">
      <div class="footer-brand"><span class="brand-mark"></span><span class="brand-name">Portals Drapes &amp; Louvres</span></div>
      <div class="footer-phone"><svg width="10" height="10"><use href="#phone"/></svg>9471 2658</div>
      <div class="footer-address"><svg width="8" height="8"><use href="#pin"/></svg>482 Upper Wattleby Road, Kestrel Heights</div>
    </footer>
  </article>

  <!-- Outdoor Awnings -->
  <article class="ad" style="left:381px;top:227px">
    <svg class="ad-visual" viewBox="0 0 235 240">
      <defs><linearGradient id="g2" x1="0" y1="0" x2="1" y2="1"><stop offset="0" stop-color="#3a3a3c"/><stop offset="0.5" stop-color="#6f8a55"/><stop offset="1" stop-color="#8d8a85"/></linearGradient></defs>
      <path d="M-3,103 A128,128 0 0 0 238,103" fill="none" stroke="#0072BC" stroke-width="6"/>
      <path d="M0,50 H235 V100 A123.7,123.7 0 0 1 0,100 Z" fill="url(#g2)" role="img" aria-label="Deck with outdoor furniture under a retractable awning, trees behind"/>
      <circle cx="117.5" cy="191" r="38" fill="url(#badge-fill)" role="img" aria-label="Gold emblem: Celebrating 13 Years in Business"/>
    </svg>
    <div class="ad-header">SALE NOW ON</div>
    <div class="product-ribbon">OUTDOOR AWNINGS</div>
    <ul class="benefits"><li class="benefits-inner">
      <span class="benefit"><svg><use href="#bullet"/></svg>Reduce Heat &amp; Glare</span>
      <span class="benefit"><svg><use href="#bullet"/></svg>Energy Saving</span>
      <span class="benefit"><svg><use href="#bullet"/></svg>Custom Made</span>
    </li></ul>
    <p class="cta">BOOK A FREE QUOTE TODAY!</p>
    <p class="offer">UP TO 40% OFF</p>
    <footer class="ad-footer">
      <div class="footer-brand"><span class="brand-mark"></span><span class="brand-name">Portals Drapes &amp; Louvres</span></div>
      <div class="footer-phone"><svg width="10" height="10"><use href="#phone"/></svg>9471 2658</div>
      <div class="footer-address"><svg width="8" height="8"><use href="#pin"/></svg>482 Upper Wattleby Road, Kestrel Heights</div>
    </footer>
  </article>

  <!-- Plantation Shutters -->
  <article class="ad" style="left:632px;top:227px">
    <svg class="ad-visual" viewBox="0 0 235 240">
      <defs><linearGradient id="g3" x1="0" y1="0" x2="1" y2="0"><stop offset="0" stop-color="#5a5d60"/><stop offset="0.5" stop-color="#d9dadb"/><stop offset="1" stop-color="#4f5256"/></linearGradient></defs>
      <path d="M-3,103 A128,128 0 0 0 238,103" fill="none" stroke="#0072BC" stroke-width="6"/>
      <path d="M0,50 H235 V100 A123.7,123.7 0 0 1 0,100 Z" fill="url(#g3)" role="img" aria-label="White plantation shutters on a tall window in a grey room"/>
      <circle cx="117.5" cy="191" r="38" fill="url(#badge-fill)" role="img" aria-label="Gold emblem: Celebrating 13 Years in Business"/>
    </svg>
    <div class="ad-header">SALE NOW ON</div>
    <div class="product-ribbon">PLANTATION SHUTTERS</div>
    <ul class="benefits"><li class="benefits-inner">
      <span class="benefit"><svg><use href="#bullet"/></svg>Modern &amp; Elegant</span>
      <span class="benefit"><svg><use href="#bullet"/></svg>Light &amp; Privacy Control</span>
      <span class="benefit"><svg><use href="#bullet"/></svg>Durable &amp; Easy Care</span>
    </li></ul>
    <p class="cta">BOOK A FREE QUOTE TODAY!</p>
    <p class="offer">FROM $299/sqm</p>
    <footer class="ad-footer">
      <div class="footer-brand"><span class="brand-mark"></span><span class="brand-name">Portals Drapes &amp; Louvres</span></div>
      <div class="footer-phone"><svg width="10" height="10"><use href="#phone"/></svg>9471 2658</div>
      <div class="footer-address"><svg width="8" height="8"><use href="#pin"/></svg>482 Upper Wattleby Road, Kestrel Heights</div>
    </footer>
  </article>

  <!-- Roller Shutters -->
  <article class="ad" style="left:128px;top:662px">
    <svg class="ad-visual" viewBox="0 0 235 240">
      <defs><linearGradient id="g4" x1="0" y1="0" x2="1" y2="0"><stop offset="0" stop-color="#7a5a44"/><stop offset="0.45" stop-color="#4a4b4e"/><stop offset="1" stop-color="#b7a58e"/></linearGradient></defs>
      <path d="M-3,103 A128,128 0 0 0 238,103" fill="none" stroke="#0072BC" stroke-width="6"/>
      <path d="M0,50 H235 V100 A123.7,123.7 0 0 1 0,100 Z" fill="url(#g4)" role="img" aria-label="Brick home exterior with closed dark roller shutters on windows"/>
      <circle cx="117.5" cy="191" r="38" fill="url(#badge-fill)" role="img" aria-label="Gold emblem: Celebrating 13 Years in Business"/>
    </svg>
    <div class="ad-header">SALE NOW ON</div>
    <div class="product-ribbon">ROLLER SHUTTERS</div>
    <ul class="benefits"><li class="benefits-inner">
      <span class="benefit"><svg><use href="#bullet"/></svg>Security Protection</span>
      <span class="benefit"><svg><use href="#bullet"/></svg>Block Heat &amp; Noise</span>
      <span class="benefit"><svg><use href="#bullet"/></svg>Total Light Control</span>
    </li></ul>
    <p class="cta">BOOK A FREE QUOTE TODAY!</p>
    <p class="offer">UP TO 40% OFF</p>
    <footer class="ad-footer">
      <div class="footer-brand"><span class="brand-mark"></span><span class="brand-name">Portals Drapes &amp; Louvres</span></div>
      <div class="footer-phone"><svg width="10" height="10"><use href="#phone"/></svg>9471 2658</div>
      <div class="footer-address"><svg width="8" height="8"><use href="#pin"/></svg>482 Upper Wattleby Road, Kestrel Heights</div>
    </footer>
  </article>

  <!-- Security Doors -->
  <article class="ad" style="left:381px;top:662px">
    <svg class="ad-visual" viewBox="0 0 235 240">
      <defs><linearGradient id="g5" x1="0" y1="0" x2="1" y2="0"><stop offset="0" stop-color="#c9c9c7"/><stop offset="0.45" stop-color="#2a2b2d"/><stop offset="0.8" stop-color="#8a9a78"/><stop offset="1" stop-color="#2f3032"/></linearGradient></defs>
      <path d="M-3,103 A128,128 0 0 0 238,103" fill="none" stroke="#0072BC" stroke-width="6"/>
      <path d="M0,50 H235 V100 A123.7,123.7 0 0 1 0,100 Z" fill="url(#g5)" role="img" aria-label="Front entry with a black mesh security door opening to the street"/>
      <circle cx="117.5" cy="191" r="38" fill="url(#badge-fill)" role="img" aria-label="Gold emblem: Celebrating 13 Years in Business"/>
    </svg>
    <div class="ad-header">SALE NOW ON</div>
    <div class="product-ribbon">SECURITY DOORS</div>
    <ul class="benefits" style="top:270px"><li class="benefits-inner">
      <span class="benefit"><svg><use href="#bullet"/></svg>3 Point Locking</span>
      <span class="benefit"><svg><use href="#bullet"/></svg>Premium Mesh</span>
      <span class="benefit"><svg><use href="#bullet"/></svg>Custom Made</span>
    </li></ul>
    <p class="cta large">ORDER NOW</p>
    <p class="offer">FROM $750</p>
    <footer class="ad-footer">
      <div class="footer-brand"><span class="brand-mark"></span><span class="brand-name">Portals Drapes &amp; Louvres</span></div>
      <div class="footer-phone"><svg width="10" height="10"><use href="#phone"/></svg>9471 2658</div>
      <div class="footer-address"><svg width="8" height="8"><use href="#pin"/></svg>482 Upper Wattleby Road, Kestrel Heights</div>
    </footer>
  </article>

  <!-- Blinds & Sheers -->
  <article class="ad" style="left:632px;top:662px">
    <svg class="ad-visual" viewBox="0 0 235 240">
      <defs><linearGradient id="g6" x1="0" y1="0" x2="1" y2="0"><stop offset="0" stop-color="#a9a6ac"/><stop offset="0.45" stop-color="#555258"/><stop offset="0.75" stop-color="#cfcdd0"/><stop offset="1" stop-color="#8d8a90"/></linearGradient></defs>
      <path d="M-3,103 A128,128 0 0 0 238,103" fill="none" stroke="#0072BC" stroke-width="6"/>
      <path d="M0,50 H235 V100 A123.7,123.7 0 0 1 0,100 Z" fill="url(#g6)" role="img" aria-label="Dining room with sheer curtains and dark drapes across glass doors"/>
      <circle cx="117.5" cy="191" r="38" fill="url(#badge-fill)" role="img" aria-label="Gold emblem: Celebrating 13 Years in Business"/>
    </svg>
    <div class="ad-header">SALE NOW ON</div>
    <div class="product-ribbon">BLINDS &amp; SHEERS</div>
    <ul class="benefits"><li class="benefits-inner">
      <span class="benefit"><svg><use href="#bullet"/></svg>Huge Range of Fabrics</span>
      <span class="benefit"><svg><use href="#bullet"/></svg>Modern Soft Finish</span>
      <span class="benefit"><svg><use href="#bullet"/></svg>Perfect for Any Room</span>
    </li></ul>
    <p class="cta">BOOK A FREE QUOTE TODAY!</p>
    <p class="offer">UP TO 40% OFF</p>
    <footer class="ad-footer">
      <div class="footer-brand"><span class="brand-mark"></span><span class="brand-name">Portals Drapes &amp; Louvres</span></div>
      <div class="footer-phone"><svg width="10" height="10"><use href="#phone"/></svg>9471 2658</div>
      <div class="footer-address"><svg width="8" height="8"><use href="#pin"/></svg>482 Upper Wattleby Road, Kestrel Heights</div>
    </footer>
  </article>
</main>
</body>
</html>
```